Residential Mortgage Leader needs Wordpress Design

Looking for a home page website design for a client. We develop using the WordPress platform and would prefer the design be at least loosely based on an existing WordPress template. Attached files have many notes from our creative brief with client. The site must be responsive. Approved, basic wireframe attached. There is room for interpretation.

Existing web site: http://www.marisolkettering.example/

The Marisol Kettering Team relies on strong systems to deliver an on-time, done-right, friendly experience. Marisol offers mortgages and refinancing services throughout the United States. She is a successful Brookvale Funding agent who strives to be an active part of her community. She would like to focus the site on her team, rather than just her.

Difference makers...
When you work with the Marisol Kettering team you get a high level of expertise and a friendly experience.

She has amazing credentials. Marisol is widely recognized as a top producer for her company, and has earned a number of awards and honors for her customer service.

Marisol's team is very engaged and enjoys sharing social comments or photos from their community.

Imagery:
* Friendly, warm imagery, preferably of her team or an image to represent her team
* Clean and crisp
* Professional / Experts in mortgage and refinance
* Clean / Good use of white space
Updates

When possible, please use imagery from the DFW area. The client mentioned they would prefer not to see stock images. Thanks.

Amend that- creative use of stock images, however, is fine. A few designs have used stock imagery, but in a well-considered manner.

We added some photos and graphics that are local. We are Dallas / Ft. Worth, Plano, Frisco, Texas. We also added some examples of photos to use for the "In the Community" area. Stock photos of business folks just doesn't fit there. Thanks!

Target Market(s)

They service a lot of builders, but also work with homeowners. Their typical client is usually a woman searching for mortgage services online. She typically has a family and may refer her husband to Marisol's team. Keep in mind, however, they also see a number of other scenarios. Most of their clients are middle to high-end borrowers.

Industry/Entity Type

It Company

Requirements
Must have
• Design should be developed using program such as Photoshop or Fireworks or Illustrator as last preference. Ideally, the design would be based on an existing responsive WordPress theme, which we would customize. You must include the name of the target theme. The footer should include lots of space for disclaimers and legal language. Site navigation should include these choices: "Home, About, Builders, Mortgage Info, Approval, Blog, Contact"
Nice to have
• Blog, social media and photos area. Use of the already approved style prototype with colors and fonts (Lato- a Google font, Times New Roman and Cookie-a decorative Google font). However, we are open to interpretation.
Should not have
• Hard to read fonts or a lack of white space.

```html
<!DOCTYPE html>
<html lang="en">
<head>
<meta charset="utf-8">
<title>Brookvale Funding — Marisol Kettering Team</title>
<link href="https://fonts.googleapis.com/css2?family=Source+Sans+3:wght@300;400;600;700&display=swap" rel="stylesheet">
<style>
:root{
  --brand:#c8321f;
  --brand-dark:#a8271a;
  --footer:#a82a1b;
  --ink:#333;
  --muted:#555;
  --grey-band:#6e6e70;
  --grey-band-dark:#5c5c5e;
  --line:#d6d6d6;
}
*{box-sizing:border-box;margin:0;padding:0}
html,body{width:1130px;height:1200px;overflow:hidden;background:#fff}
body{position:relative;font-family:"Source Sans 3",sans-serif;color:var(--ink)}
.abs{position:absolute}

.brand{left:148px;top:28px}
.brand-name{font-size:29px;font-weight:700;color:var(--brand);letter-spacing:-.5px;line-height:1;display:flex;align-items:center;gap:8px}
.brand-mark{width:18px;height:18px;background:var(--brand);border-radius:50%}
.brand-sub{font-size:13px;color:#555;font-weight:600;margin-top:5px}

.contact-top{left:842px;top:14px}
.contact-top svg{position:absolute;left:0;top:6px}
.contact-top .lbl{margin-left:34px;font-size:16px;color:#555;font-weight:300}
.contact-top .phone{margin-left:32px;font-size:17px;color:var(--brand);font-weight:300}
.contact-top .mail{margin-left:34px;font-size:11px;color:#333}

.nav{left:145px;top:78px;width:839px;height:32px;background:linear-gradient(#d63c26,#c22e1c);display:flex}
.nav a{color:#fff;text-decoration:none;font-size:14px;display:flex;align-items:center;justify-content:center;border-right:1px solid #9c2416}
.nav a:last-child{border-right:0}

.hero{left:145px;top:116px;width:839px;height:299px;border:1px solid #ddd;background:linear-gradient(#fafafa,#e4e4e5)}
.hero-photo{left:42px;top:36px;width:356px;height:228px;border:3px solid #fff;box-shadow:0 1px 5px rgba(0,0,0,.3);background:linear-gradient(135deg,#c9b890,#6c7c88 55%,#2f3f60)}
.hero-title{left:429px;top:47px;font-size:29px;font-weight:300;color:var(--brand)}
.hero-text{left:431px;top:92px;width:330px;font-size:13px;line-height:22px;color:#444;font-weight:300}
.btn{left:434px;top:174px;width:98px;height:36px;background:var(--brand);color:#fff;font-size:15px;display:flex;align-items:center;justify-content:center;box-shadow:0 2px 3px rgba(0,0,0,.25)}
.alt-link{left:544px;top:182px;font-size:15px;color:#222}
.alt-link span{color:var(--brand)}
.dots{left:730px;top:274px;display:flex;gap:7px}
.dots i{width:12px;height:12px;border-radius:50%;border:1px solid #888;background:#fff}
.dots i.on{background:var(--brand);border-color:var(--brand)}

.band{left:145px;top:420px;width:839px;height:153px;background:linear-gradient(var(--grey-band),var(--grey-band-dark));display:flex;box-shadow:0 14px 18px -10px rgba(0,0,0,.25)}
.band-col{padding:24px 0 0 34px;color:#fff;position:relative}
.band-col+.band-col{border-left:1px solid #888}
.band-col h3{font-size:18px;font-weight:600;margin-bottom:14px}
.band-col p{font-size:12.5px;line-height:19px;font-weight:300;width:230px}
.play{position:absolute;left:230px;top:96px;width:22px;height:22px;border-radius:50%;background:#fff}

.section-title{left:0;width:1130px;top:600px;text-align:center;font-size:21px;font-weight:300;color:var(--brand)}
.section-sub{left:0;width:1130px;top:632px;text-align:center;font-size:13px;color:#555;font-weight:300}

.h-col{font-size:18px;font-weight:300;color:var(--brand)}
.blog-list{left:146px;top:725px;list-style:none}
.blog-list li{font-size:13.5px;color:#444;font-weight:300;height:30.5px;padding-left:19px;position:relative}
.blog-list li::before{content:"";position:absolute;left:4px;top:6px;border-left:4px solid #555;border-top:3px solid transparent;border-bottom:3px solid transparent}

.social-item{left:357px;width:300px;height:58px}
.thumb{position:absolute;left:0;top:0;width:58px;height:58px}
.social-item p{position:absolute;left:74px;top:0;width:210px;font-size:11.5px;line-height:17.4px;color:#222}

.community{left:712px;top:682px;width:277px;height:243px;border:1px solid #ccc;background:linear-gradient(#fff,#f3f3f3);box-shadow:0 0 4px rgba(0,0,0,.12)}
.community .h-col{position:absolute;left:20px;top:20px;font-size:17px}
.member{position:absolute;width:76px;text-align:center}
.member .pic{width:76px;height:64px;border:1px solid #ccc}
.member span{display:block;font-size:13px;color:#333;margin-top:7px}

.footer{left:153px;top:977px;width:835px;height:223px;background:var(--footer);color:#fff}
.f-col{position:absolute;top:20px}
.f-col h4{font-size:13px;font-weight:600;margin-bottom:8px}
.f-col p{font-size:11.5px;line-height:19px;font-weight:300}
.agent-photo{position:absolute;left:504px;top:24px;width:88px;height:111px;background:linear-gradient(#6b4a38,#c9a68d 60%,#3a2a22)}
.f-rule{position:absolute;left:22px;top:149px;width:790px;height:1px;background:#7e1d12}
.housing{position:absolute;left:28px;top:160px;width:58px;height:54px;border:2px solid #fff}
.copy{position:absolute;left:529px;top:178px;font-size:11.5px;font-weight:300}
.soc{position:absolute;top:171px;width:23px;height:23px;border-radius:50%;border:1px solid rgba(255,255,255,.6)}
</style>
</head>
<body>

<header>
  <div class="abs brand">
    <div class="brand-name">Brookvale Funding <i class="brand-mark"></i></div>
    <div class="brand-sub">A Ridgeline Capital Company</div>
  </div>
  <div class="abs contact-top">
    <svg width="22" height="28" viewBox="0 0 22 28"><path d="M6 2c2 0 3 1 3 3l1 5c0 1-2 2-2 3 0 3 3 8 6 9 1 0 2-2 3-2l3 2c1 1 1 3 0 4-1 1-3 2-5 2C7 27 2 16 2 7c0-3 2-5 4-5z" fill="#aaa"/></svg>
    <div class="lbl">Work with us</div>
    <div class="phone">123 - 456 - 7890</div>
    <div class="mail">E mail here</div>
  </div>
  <nav class="abs nav">
    <a style="width:104px">Home</a>
    <a style="width:109px">About</a>
    <a style="width:107px">Builders</a>
    <a style="width:114px">Mortgage Info</a>
    <a style="width:127px">Approval</a>
    <a style="width:134px">Blog</a>
    <a style="width:144px">Contact Us</a>
  </nav>
</header>

<section class="abs hero">
  <div class="abs hero-photo" role="img" aria-label="Young man working at a desk in a bright office"></div>
  <h1 class="abs hero-title">Earning Your Business</h1>
  <p class="abs hero-text">Lorem Ipsum is simply dummy text of the printing and typesetting industry. Lorem Ipsum has been the industry's standard dummy text ever since</p>
  <div class="abs btn">Start Here</div>
  <div class="abs alt-link">or <span>Get to Know Us</span></div>
  <div class="abs dots"><i></i><i></i><i class="on"></i><i></i><i></i></div>
</section>

<section class="abs band">
  <div class="band-col" style="width:277px">
    <h3>Our Credentials</h3>
    <p>Lorem Ipsum is simply dummy text of the printing and typesetting industry. Lorem Ipsum has been the industry's</p>
    <svg class="play" viewBox="0 0 22 22"><circle cx="11" cy="11" r="11" fill="#fff"/><path d="M9 6.5l6 4.5-6 4.5z" fill="#555"/></svg>
  </div>
  <div class="band-col" style="width:280px;padding-left:40px">
    <h3>Awards</h3>
    <p>Lorem Ipsum is simply dummy text of the printing and typesetting industry. Lorem Ipsum has been the industry's</p>
  </div>
  <div class="band-col" style="width:282px;padding-left:50px">
    <h3>Recognion</h3>
    <p>Lorem Ipsum is simply dummy text of the printing and typesetting industry. Lorem Ipsum has been the industry's</p>
  </div>
</section>

<h2 class="abs section-title">Engaged in Our Community</h2>
<p class="abs section-sub">Connect with us</p>

<h3 class="abs h-col" style="left:146px;top:688px">Blog Post</h3>
<ul class="abs blog-list">
  <li>Borawing</li><li>Best Practices</li><li>Annancements</li><li>Resources</li><li>How to guides</li><li>Builders info</li>
</ul>

<h3 class="abs h-col" style="left:356px;top:678px">Social</h3>
<div class="abs social-item" style="top:715px">
  <div class="thumb" role="img" aria-label="Family in front of a sold home sign" style="background:linear-gradient(#4d6b3a,#b09070)"></div>
  <p>Lorem Ipsum is simply dummy text of the printing and typesetting Contrary to popular belief, Lorem Ipsum is not simply</p>
</div>
<div class="abs social-item" style="top:791px">
  <div class="thumb" role="img" aria-label="Small model house held in hands" style="background:linear-gradient(#e6e2dc,#b65a3a)"></div>
  <p>Lorem Ipsum is simply dummy text of the printing and typesetting Contrary to popular belief, Lorem Ipsum is not simply</p>
</div>
<div class="abs social-item" style="top:867px">
  <div class="thumb" role="img" aria-label="Portrait of a smiling woman" style="background:linear-gradient(#5a3c2e,#c8a088)"></div>
  <p>Lorem Ipsum is simply dummy text of the printing and typesetting Contrary to popular belief, Lorem Ipsum is not simply</p>
</div>

<aside class="abs community">
  <h3 class="h-col">In the Community</h3>
  <div class="member" style="left:19px;top:45px"><div class="pic" role="img" aria-label="Team member portrait" style="background:linear-gradient(#f2f2f2,#8a8a8a)"></div><span>Name</span></div>
  <div class="member" style="left:103px;top:45px"><div class="pic" role="img" aria-label="Team member portrait" style="background:linear-gradient(#dfe8f0,#5a6f9a)"></div><span>Name</span></div>
  <div class="member" style="left:188px;top:45px"><div class="pic" role="img" aria-label="Team member portrait" style="background:linear-gradient(#f4f0ea,#b08a70)"></div><span>Name</span></div>
  <div class="member" style="left:19px;top:143px"><div class="pic" role="img" aria-label="Team member portrait" style="background:linear-gradient(#b88a6a,#2a2a2a)"></div><span>Name</span></div>
  <div class="member" style="left:103px;top:143px"><div class="pic" role="img" aria-label="Team member portrait" style="background:linear-gradient(#5a5a5a,#d0b098)"></div><span>Name</span></div>
  <div class="member" style="left:188px;top:143px"><div class="pic" role="img" aria-label="Team member portrait" style="background:linear-gradient(#6f86b5,#4a3a30)"></div><span>Name</span></div>
</aside>

<footer class="abs footer">
  <div class="f-col" style="left:28px"><h4>Contact Us</h4><p>Corporate Office - 4720 Meadowline Road,<br>Suite 600 Dallas,<br>Texas 75252</p></div>
  <div class="f-col" style="left:258px"><h4>Language</h4><p>English<br>French<br>German<br>Russian</p></div>
  <div class="f-col" style="left:384px"><h4>Links</h4><p>Home<br>About<br>Builders<br>Approval<br>Contact Us</p></div>
  <div class="agent-photo" role="img" aria-label="Portrait of Marisol Kettering"></div>
  <div class="f-col" style="left:605px"><h4 style="margin-bottom:2px">Marisol Kettering</h4><p style="font-weight:600;margin-bottom:8px">Branch Manager</p><p>Office: 469.555.0142 &nbsp;|&nbsp; Cell: 866.555.0190<br>mkettering@brookvalefunding.example<br>NMLS: 40219<br>2280 Lakeview Plaza, Ste. 140, Frisco, TX 75034</p></div>
  <div class="f-rule"></div>
  <div class="housing" role="img" aria-label="Equal housing badge"></div>
  <div class="copy">Copyrights @ 2013 All Rights Reserved</div>
  <span class="soc" style="left:740px;background:#2d5fa8"></span>
  <span class="soc" style="left:772px;background:#e8892a"></span>
  <span class="soc" style="left:804px;background:#48a8dc"></span>
</footer>

</body>
</html>
```